Business Card Design Project

Actor, Producer, Vocal Coach, Choral Director, Song WriterPhone: (215) 555-0142 Fax: (215) 856-3933Email: waltierblocker@gmail.comFacebook: facebook.com/waltier.blockerTwitter: @thedf482

Industry/Entity Type

Business

Contact Information for Business Card

Business Cards that include my picture

Colors

Designer to choose colors to be used in the design.

```html
<!DOCTYPE html>
<html lang="en">
<head>
<meta charset="utf-8">
<title>Dorian Fellsmore – Business Card</title>
<link href="https://fonts.googleapis.com/css2?family=Montserrat:wght@400;700&display=swap" rel="stylesheet">
<style>
  :root {
    --stage: #111111;
    --card-white: #ffffff;
    --card-black: #050505;
    --ink: #111111;
    --ink-soft: #2a2a2a;
    --divider: #cfcfcf;
    --photo-top: #bdb3b6;
    --photo-bottom: #8c8589;
    --icon-blue: #3b5998;
    --icon-sky: #4fb3e8;
  }
  * { margin: 0; padding: 0; box-sizing: border-box; }
  html, body {
    width: 1200px; height: 1000px; overflow: hidden;
    background: var(--stage);
    font-family: "Montserrat", Arial, sans-serif;
  }
  .stage { position: relative; width: 1200px; height: 1000px; }
  .card {
    position: absolute; top: 350px;
    width: 525px; height: 300px;
    box-shadow: 0 12px 30px rgba(0,0,0,.6);
  }
  .card--front { left: 50px; background: var(--card-white); }
  .card--back {
    left: 625px;
    background: linear-gradient(135deg, #0d0d0d 0%, var(--card-black) 60%);
    display: flex; align-items: center; justify-content: center;
  }
  .portrait {
    position: absolute; left: 26px; top: 28px;
    width: 236px; height: 244px;
    background: linear-gradient(180deg, var(--photo-top), var(--photo-bottom));
  }
  .divider {
    position: absolute; left: 268px; top: 0;
    width: 9px; height: 300px;
    background: var(--divider);
  }
  .details {
    position: absolute; left: 290px; right: 24px; top: 58px;
    text-align: right; color: var(--ink);
  }
  .details__name { font-weight: 700; font-size: 21px; letter-spacing: .2px; white-space: nowrap; }
  .details__roles {
    font-size: 11px; line-height: 1.4; color: var(--ink-soft);
    margin-top: 2px;
  }
  .contact-list {
    list-style: none; margin-top: 26px;
    font-size: 11px; line-height: 1.1;
  }
  .contact-list li {
    display: flex; justify-content: flex-end; align-items: center;
    gap: 6px; margin-bottom: 4px; white-space: nowrap;
  }
  .contact-icon {
    width: 14px; height: 14px; border-radius: 50%;
    background: var(--ink);
    display: inline-flex; align-items: center; justify-content: center;
    flex: none;
  }
  .contact-icon--social { background: var(--icon-blue); }
  .contact-icon--handle { background: var(--icon-sky); }
  .back-name { color: #ffffff; font-weight: 700; font-size: 30px; letter-spacing: .5px; }
</style>
</head>
<body>
<main class="stage">
  <section class="card card--front">
    <div class="portrait" role="img" aria-label="Portrait photo of Dorian Fellsmore in a grey suit and pink tie"></div>
    <div class="divider"></div>
    <div class="details">
      <h1 class="details__name">Dorian Fellsmore</h1>
      <p class="details__roles">Actor, Producer, Vocal Coach<br>Choral Director, Song Writer</p>
      <ul class="contact-list">
        <li>(215) 555-0142
          <span class="contact-icon"><svg width="8" height="8" viewBox="0 0 10 10"><path d="M2 1l2 2-1 1.2c.6 1.3 1.5 2.2 2.8 2.8L7 6l2 2-1.2 1.5C4.5 9 1 5.5.5 2.2z" fill="#fff"/></svg></span></li>
        <li>(215) 555-0187
          <span class="contact-icon"><svg width="8" height="8" viewBox="0 0 10 10"><rect x="1" y="3" width="8" height="5" fill="#fff"/><rect x="3" y="1" width="4" height="2" fill="#fff"/></svg></span></li>
        <li>dorianfellsmore@postlane.net
          <span class="contact-icon"><svg width="8" height="8" viewBox="0 0 10 10"><rect x="1" y="2" width="8" height="6" fill="none" stroke="#fff" stroke-width="1.2"/><path d="M1 2l4 3.5L9 2" fill="none" stroke="#fff" stroke-width="1.2"/></svg></span></li>
        <li>dorian.fellsmore <span class="contact-icon contact-icon--social"></span></li>
        <li>@thedf482 <span class="contact-icon contact-icon--handle"></span></li>
      </ul>
    </div>
  </section>
  <section class="card card--back">
    <span class="back-name">Dorian Fellsmore</span>
  </section>
</main>
</body>
</html>
```